Website for a company offering full serivce charging solutions for electric cars

The company "tanu-werk" (english: "tanu-works") offering all-in-one-solutions for charging infrastructure for electric mobility.

There are four products:
1- Wallboxes for single-family homes
2- Solutions for property devloper/-management for property parking space
3- All-in-one-charging solution for municipalities/communities
4- Solutions for tourism/hotels/holiday appartments

The Website structure:
1. Main Page
2.1. Product Page Single Homes
2.2. Product Page Property Management / Parking
2.3. Product Page Municipality
2.4. Product Page Tourism
3. Contact Form / Request for information
4. Imprint / Legal

The Website should be built on Wordpress with a powerful possibility to simply add/modify specific landing pages.

We would like you to implement the website later and also maintain it if possible, but we would be able to do minor modifications by ourselfs (for A/B-Testing)

The website should be clear and simple, easy to understand.
Target group is mainly B2C without deeper knowledge of that topic.

It should suggest, that we will provide a very simple way to get the charging infrastructure done.

We need a contact form, maybe we will use Hubspot later.

Attached you will find a draft of the main page and a landing page (for 2.2) - it is just the content, please ignore the design. We would love to let you create a suitable design.
Also you will find some drafts a bit different for the same story.

I added also a few stock photos, but they don't need to be used! If you have better ideas, you are welcome!

Industry/Entity Type

Charging/Electric mobility

Number of Pages Required

2 page

Font styles to use
Sans Serif

Requirements
Must have
• Based on Wordpress, and the designer should be able to implement it on Wordpress on a later step

```html
<!DOCTYPE html>
<html lang="de">
<head>
<meta charset="utf-8">
<title>tanu-werk – einfach mehr als laden</title>
<link href="https://fonts.googleapis.com/css2?family=Titillium+Web:wght@300;400;600;700&family=Montserrat:wght@400;500;600&display=swap" rel="stylesheet">
<style>
:root{
  --bg:#121827;
  --bg-deep:#0d1220;
  --magenta:#e0249a;
  --purple:#8a3fd1;
  --violet:#6a2fb8;
  --ring:#3a1f55;
  --text:#ffffff;
  --muted:#c9cbd6;
  --footer:#151b2a;
  --bar:#232a38;
}
*{box-sizing:border-box;margin:0;padding:0}
html,body{width:1200px;height:4266px;overflow:hidden}
body{background:var(--bg);color:var(--text);font-family:'Montserrat',Arial,sans-serif;position:relative}
.abs{position:absolute}
h1,h2,h3,.nav,.btn,.footer-title{font-family:'Titillium Web',Arial,sans-serif}

/* header */
.brand{left:100px;top:32px;display:flex;align-items:center;gap:12px}
.brand-dot{width:46px;height:46px;border-radius:50%;background:var(--magenta)}
.brand-name{font-family:'Titillium Web',sans-serif;font-size:28px;font-weight:400;line-height:1}
.brand-tag{font-size:13px;color:var(--muted);margin-top:4px}
.nav{left:456px;top:44px;display:flex;gap:0;font-size:17px}
.nav a{color:#fff;text-decoration:none;width:130px;text-align:center;display:inline-block;padding-bottom:8px}
.nav a.active{border-bottom:2px solid var(--magenta);width:72px;margin:0 29px}
.btn-contact{left:965px;top:36px;width:125px;height:40px;border-radius:20px;background:linear-gradient(90deg,var(--violet),var(--magenta));font-family:'Titillium Web',sans-serif;font-weight:700;font-size:17px;display:flex;align-items:center;justify-content:center;box-shadow:0 0 18px rgba(224,36,154,.6)}

/* hero */
.hero-title{top:160px;left:0;width:1200px;text-align:center;font-size:50px;font-weight:700;color:var(--magenta);letter-spacing:.5px}
.hero-title span{font-weight:300;color:var(--purple)}
.hero-sub{top:234px;left:0;width:1200px;text-align:center;font-size:24px;font-family:'Titillium Web',sans-serif;font-weight:300;line-height:1.2}
.hero-art{left:80px;top:340px;width:1000px;height:350px;background:radial-gradient(ellipse at 55% 70%,#2fa9e6 0%,#1a4e8a 25%,#16223d 55%,transparent 75%)}

/* glows */
.glow{border-radius:50%;filter:blur(60px)}

/* intro */
.intro-title{left:126px;top:785px;font-size:36px;font-weight:700;color:var(--magenta)}
.intro-title span{font-weight:300;color:var(--purple)}
.intro-lead{left:126px;top:842px;width:530px;font-size:19px;font-weight:600;line-height:1.5}
.intro-body{left:126px;top:985px;width:530px;font-size:14px;line-height:2}

/* circles */
.circle-outer{border-radius:50%;background:var(--ring)}
.circle-ring{border-radius:50%;border:2px solid var(--magenta);box-shadow:0 0 0 6px rgba(138,63,209,.35)}
.photo{border-radius:50%}

.ask{top:1255px;left:0;width:1200px;text-align:center;font-size:28px;font-weight:600;line-height:1.25;text-transform:uppercase}

.sec-title{font-size:34px;font-weight:600;text-transform:uppercase}
.sec-title span{color:var(--magenta);font-weight:400}

.plain-list{list-style:none;font-size:13.5px;line-height:1.4;color:#e8e9ef}
.plain-list li{margin-bottom:10px}
.chev-list{list-style:none;font-size:13.5px;line-height:1.4;color:#e8e9ef}
.chev-list li{position:relative;padding-left:16px;margin-bottom:9px}
.chev-list li::before{content:"";position:absolute;left:0;top:5px;width:6px;height:6px;border-right:2px solid var(--magenta);border-top:2px solid var(--magenta);transform:rotate(45deg)}
.sub-list{list-style:none;padding-left:28px;margin-top:8px}
.sub-list li{padding:0;margin:0}
.sub-list li::before{display:none}

.grid-band{left:0;width:1200px;background:linear-gradient(180deg,transparent,rgba(138,63,209,.25) 50%,transparent)}

/* contact */
.contact{left:0;top:3295px;width:1200px;height:595px;background:linear-gradient(100deg,#d41c9a 0%,#b020b0 35%,#6a2fb8 60%,#1c2150 85%,#121827 100%)}
.contact-title{left:113px;top:3375px;font-size:38px;font-weight:600}
.contact-title span{font-weight:300}
.contact-rule{left:116px;top:3425px;width:60px;height:3px;background:#fff}
.contact-text{left:116px;top:3447px;width:480px;font-size:15px;line-height:1.4}
.field{background:#fff;color:#666;font-size:12px;padding:12px 16px;height:40px}
.btn-submit{left:126px;top:3723px;width:180px;height:50px;border:2px solid #fff;font-family:'Titillium Web',sans-serif;font-weight:700;font-size:17px;display:flex;align-items:center;justify-content:center}
.contact-art{left:600px;top:3330px;width:560px;height:560px;background:radial-gradient(ellipse at 60% 50%,#b9a6ff 0%,#5c57d6 25%,#2b2f7a 50%,transparent 72%)}

/* footer */
.footer-brand{left:110px;top:3945px;text-align:center;width:220px}
.footer-brand .brand-dot{margin:0 auto 12px;width:60px;height:60px}
.footer-brand .brand-name{font-size:38px}
.vline{width:1px;background:#2a3142}
.footer-col{top:3965px}
.footer-title{font-size:18px;font-weight:700;border-left:3px solid var(--magenta);padding-left:22px;margin-left:-25px;margin-bottom:14px}
.footer-col a{display:block;color:#a9adbb;font-size:15px;text-decoration:none;margin-bottom:14px}
.social{display:flex;gap:7px}
.social span{width:34px;height:34px;border-radius:50%;background:var(--magenta)}
.bottom-bar{left:0;top:4190px;width:1200px;height:76px;background:var(--bar);display:flex;align-items:center;justify-content:center;font-size:14px;color:#d0d2da}
</style>
</head>
<body>

<!-- backdrop glows -->
<div class="abs glow" style="left:-120px;top:700px;width:420px;height:520px;background:rgba(224,36,154,.25)"></div>
<div class="abs glow" style="left:1000px;top:1000px;width:360px;height:500px;background:rgba(138,63,209,.35)"></div>
<div class="abs glow" style="left:-150px;top:2250px;width:400px;height:500px;background:rgba(138,63,209,.3)"></div>

<!-- header -->
<div class="abs brand">
  <div class="brand-dot"></div>
  <div><div class="brand-name">tanu-werk.de</div><div class="brand-tag">einfach mehr als laden</div></div>
</div>
<nav class="abs nav">
  <a class="active" href="#">Lösungen</a><a href="#">Unternehmen</a><a href="#">Services</a><a href="#">Karriere</a>
</nav>
<div class="abs btn-contact">Kontakt</div>

<!-- hero -->
<h1 class="abs hero-title">TANU-WERK IST <span>IHR PARTNER</span></h1>
<p class="abs hero-sub">wenn das Laden nicht nur einfach, sondern die Umsetzung<br>auch aus einer Hand kommen soll</p>
<div class="abs hero-art" role="img" aria-label="Elektroauto an Ladesäulen mit leuchtender Batterie"></div>

<!-- intro -->
<h2 class="abs intro-title">ORVIT <span>TANU WERK</span></h2>
<p class="abs intro-lead">Wir bieten Lösungen sowohl für Privatkunden, Geschäftskunden als auch Kommunen an, die schnell, fair und ohne Eigenleistung zu einer smarten Ladelösung für E-Fahrzeuge kommen möchten.</p>
<p class="abs intro-body">Von der Beratung, über die Installation, Inbetriebnahme bis zur Abrechnung und Wartung bekommen Sie bei tanu-werk alles aus einer Hand. Auf Wunsch vermieten wir auch die Ladetechnik und übernehmen im gewerblichen Bereich die direkte Abrechnung mit dem Nutzer. Für Kommunen bieten wir den kostenfreien Full-Service an und beteiligen die Gemeinden an der Nutzung der Infrastruktur.</p>

<div class="abs circle-outer" style="left:675px;top:730px;width:440px;height:440px"></div>
<div class="abs circle-ring" style="left:685px;top:772px;width:380px;height:380px"></div>
<div class="abs photo" role="img" aria-label="Leuchtender Ladestecker an einem E-Fahrzeug" style="left:700px;top:787px;width:350px;height:350px;background:radial-gradient(circle at 55% 45%,#5aa0ff,#1f3fa8 45%,#0e1c5a)"></div>

<h2 class="abs ask">Fragen Sie uns nach der auf Ihre individuellen<br>Bedürfnisse zugeschnittenen Lösung:</h2>

<!-- Privatkunde -->
<div class="abs circle-outer" style="left:115px;top:1375px;width:460px;height:460px"></div>
<div class="abs circle-ring" style="left:137px;top:1417px;width:380px;height:380px"></div>
<div class="abs photo" role="img" aria-label="Wallbox mit blau leuchtendem Ladekabel" style="left:152px;top:1432px;width:350px;height:350px;background:radial-gradient(circle at 55% 50%,#3b6cff,#8fa4d8 40%,#e6e3e0 70%)"></div>
<h2 class="abs sec-title" style="left:600px;top:1435px"><span>Als</span> Privatkunde</h2>
<ul class="abs plain-list" style="left:600px;top:1505px;width:500px">
  <li>Bestandsanalyse mit umfangreicher Beratung über die Möglichkeiten der Umsetzung</li>
  <li>Prüfung und Übernahme der Anmeldung verfügbarer Fördermöglichkeiten</li>
  <li>Auswahl an smarten Wallbox Lösungen, passend für Ihr Fahrzeug und Ihre Bedürfnisse</li>
  <li>Installation inkl. aller notwendigen Materialien und Tätigkeiten (Durchbrüche, Erdarbeiten, etc.)</li>
  <li>Inbetriebnahme und Einweisung in die Ladetechnik</li>
  <li>Jährlich technische Wartung nach DGUV3</li>
  <li>Reparaturservice, unter Berücksichtigung der geltenden Garantie Ansprüche</li>
</ul>

<div class="abs grid-band" style="top:1790px;height:150px"></div>
<div class="abs grid-band" style="top:2440px;height:150px"></div>
<div class="abs grid-band" style="top:3060px;height:200px"></div>

<!-- connectors -->
<svg class="abs" style="left:0;top:1830px" width="1200" height="820" viewBox="0 0 1200 820" fill="none" stroke="#b03aa8" stroke-width="3">
  <path d="M428 0 V90 Q428 100 470 100 H820 Q848 100 848 140 V165"/>
  <path d="M838 165 h20 v12 a10 10 0 0 1 -20 0 z M848 187 v14 M842 165 v-8 M854 165 v-8"/>
  <path d="M845 640 V700 Q845 730 810 730 H460 Q425 730 425 770 V790"/>
  <path d="M415 790 h20 v12 a10 10 0 0 1 -20 0 z M425 812 v8 M419 790 v-8 M431 790 v-8"/>
</svg>

<!-- Geschäftskunde -->
<h2 class="abs sec-title" style="left:134px;top:1976px"><span>Als</span> Geschäftskunde</h2>
<ul class="abs chev-list" style="left:134px;top:2045px;width:520px">
  <li>Durchführung einer individuellen Bedarfsanalyse inkl. Ermittlung der Anforderungen für:
    <ul class="sub-list"><li>Haus- und Immobilienverwaltungen</li><li>Dienstleistungs- und Handelsunternehmen</li><li>Hotel und Beherbergungsbetriebe</li><li>Parkraum- und Parkhausbetreiber</li><li>Tourismus, Sport- und Freizeiteinrichtungen</li></ul></li>
  <li>Planung und Projektierung des Installationsaufwands inkl. Materialverbrauch</li>
  <li>Leasing oder Kauf der Hardware</li>
  <li>Normgerechte Installation der Ladeinfrastruktur inkl. Durchbruch-, Brandschutz- und Erdarbeiten</li>
  <li>Bei Bestandsbauten Integration der Ladeinfrastruktur in die Gebäudesystemtechnik und ggf. Anpassung des Netzanschlusses</li>
  <li>Inbetriebnahme der Anlage inkl. Prüf- und Messprotokollen</li>
  <li>Wiederkehrende technische Prüfung der Anlage nach DGUV 3</li>
  <li>Austausch und Reparatur Service</li>
  <li>Unterstützung bei der mtl. Nutzungsabrechnung und Einbindung in Ihre vorhandene Abrechnungssysteme</li>
  <li>ODER direkte Abrechnung mit den Nutzern</li>
</ul>
<div class="abs circle-outer" style="left:655px;top:2015px;width:460px;height:460px"></div>
<div class="abs circle-ring" style="left:690px;top:2055px;width:380px;height:380px"></div>
<div class="abs photo" role="img" aria-label="Ladekabel mit rot leuchtender Buchse am Fahrzeug" style="left:705px;top:2070px;width:350px;height:350px;background:radial-gradient(circle at 40% 55%,#ff7a4a,#7e9ac4 30%,#dbe6f2 70%)"></div>

<!-- Kommune -->
<div class="abs circle-outer" style="left:100px;top:2680px;width:460px;height:460px"></div>
<div class="abs circle-ring" style="left:152px;top:2722px;width:380px;height:380px"></div>
<div class="abs photo" role="img" aria-label="Öffentliche Ladesäule mit blau leuchtendem Stecker" style="left:167px;top:2737px;width:350px;height:350px;background:radial-gradient(circle at 50% 50%,#4a8cff,#6d8fc2 40%,#cfe0ef 75%)"></div>
<h2 class="abs sec-title" style="left:605px;top:2652px"><span>Als</span> Kommune</h2>
<ul class="abs chev-list" style="left:612px;top:2717px;width:510px">
  <li>Konzeptionierung möglicher Ladeinfrastrukturen innerhalb Ihrer Gemeinde</li>
  <li>Planung und Projektsteuerung inkl. sämtlicher behördlicher Genehmigungsverfahren und Beantragung von Fördermitteln</li>
  <li>Fachgerechte Installation und Inbetriebnahme</li>
  <li>Regelmäßige Wartung gemäß Vorschrif</li>
  <li>Reparatur und Kundenservice</li>
  <li>Direkte Abrechnung mit dem Nutzer</li>
  <li>Beteiligung der Gemeinde am Umsatz</li>
  <li>Möglichkeit der Integration von Bonusprogrammen, mit denen der lokale Einzelhandel beworben wird</li>
  <li>von Fördermitteln</li>
  <li>Fachgerechte Installation und Inbetriebnahme</li>
  <li>Regelmäßige Wartung gemäß Vorschrif</li>
  <li>Reparatur und Kundenservice</li>
  <li>Direkte Abrechnung mit dem Nutzer</li>
  <li>Beteiligung der Gemeinde am Umsatz</li>
  <li>Möglichkeit der Integration von Bonusprogrammen, mit denen der lokale Einzelhandel beworben wird</li>
</ul>

<!-- contact -->
<section class="abs contact"></section>
<div class="abs contact-art" role="img" aria-label="Hand hält Smartphone mit leuchtendem Elektroauto und Stadtsilhouette"></div>
<h2 class="abs contact-title">CONTACT <span>US</span></h2>
<div class="abs contact-rule"></div>
<p class="abs contact-text">Lorem ipsum dolor sit amet, consectetur adipiscing elit, sed do eiusmod tempor incididunt ut labore et dolore magna aliqua.</p>
<div class="abs field" style="left:116px;top:3513px;width:236px">First Name</div>
<div class="abs field" style="left:359px;top:3513px;width:237px">Last Name</div>
<div class="abs field" style="left:116px;top:3566px;width:236px">Email address</div>
<div class="abs field" style="left:359px;top:3566px;width:237px">Phone number</div>
<div class="abs field" style="left:116px;top:3620px;width:480px;height:92px">Message</div>
<div class="abs btn-submit">SUBMIT NOW</div>

<!-- footer -->
<div class="abs footer-brand"><div class="brand-dot"></div><div class="brand-name">tanu-werk.de</div></div>
<div class="abs vline" style="left:393px;top:3890px;height:270px"></div>
<div class="abs vline" style="left:653px;top:3890px;height:270px"></div>
<div class="abs vline" style="left:868px;top:3890px;height:270px"></div>
<div class="abs footer-col" style="left:420px"><div class="footer-title">NAVIGATION</div><a href="#">AGB</a><a href="#">Datenschutzerklärung</a><a href="#">Impressum</a></div>
<div class="abs footer-col" style="left:676px"><div class="footer-title">RESOURCES</div><a href="#">Kontakt</a><a href="#">Karriere</a><a href="#">FAQs</a></div>
<div class="abs footer-col" style="left:888px"><div class="footer-title">FOLLOW US</div>
  <div class="social" aria-label="Soziale Netzwerke"><span></span><span></span><span></span><span></span></div></div>
<div class="abs bottom-bar">© 2022 tanu-werk GmbH</div>

</body>
</html>
```